all natural handmade soap company looking for unique stand out packaging design for bar soaps

we are looking for a unique and stand out on the shelf package design for our hand made soaps for grocery stores. we have a package soap box (picture included) but we are looking for a TOP-NOTCH, CUSTOM, STAND OUT DESIGN FOR THEM. I am supplying our current packaging design, but we want something more unique and STAND OUT. PICTURES i AM INCLUDING ARE: 1: OUR CURRENT PACKAGE DESIGN
2: OUR LIQUID SOAP LABELS (WHICH WE LOVE) AND WOULD LIKE THE BAR SOAPS TO BE SIMILAR
3: WILL BE IN A WHITE BOX WITH A LARGE CUT OUT IN FRONT (SEE SAMPLE BOX BROWN KRAFT).

Target Market(s)

VARIOUS CUSTOMERS. We sell to bright lantern grocers and various grocery stores

Industry/Entity Type

It Company

Requirements
Must have
• cool, unique look that will stand out from a store shelf
• full color acceptable
• our logo on the round part of the package (front)
• please leave a space for bar codes (usually on bottom of box)
• there is a cut out (front) that is there for people to see, feel and smell the soap
• be creative think outside the box open to fresh new designs
Nice to have
• metallic crescent moon (our logo)
Should not have
• organic cannot appear on the front

```html
<!DOCTYPE html>
<html lang="en">
<head>
<meta charset="utf-8">
<title>Willowmere Bar Soap Packaging</title>
<link rel="stylesheet" href="https://fonts.googleapis.com/css2?family=Cinzel:wght@400;500&family=Amatic+SC:wght@700&family=Homemade+Apple&family=Lato:wght@400&display=swap">
<style>
  :root {
    --stage: #929098;
    --paper: #ffffff;
    --ink: #1e1e1e;
    --sage: #b5bd92;
    --soap-light: #e8cfa2;
    --soap-dark: #d3b080;
    --crimson: #c40d3c;
    --brick: #8a2f25;
    --sun: #fbd434;
    --coral: #f26b4e;
  }
  html, body {
    margin: 0;
    width: 1200px;
    height: 874px;
    overflow: hidden;
    background: var(--stage);
  }
  .canvas { position: relative; width: 1200px; height: 874px; }
  .defs { position: absolute; width: 0; height: 0; }

  .panel {
    position: absolute;
    width: 222px;
    height: 318px;
    background: var(--paper);
    box-shadow: 3px 4px 6px rgba(0,0,0,0.18);
  }
  .panel::after {
    content: "";
    position: absolute;
    top: 0; right: -14px;
    width: 14px; height: 100%;
    background: var(--accent);
  }
  .panel--crimson { --accent: var(--crimson); }
  .panel--brick { --accent: var(--brick); }
  .panel--sun { --accent: var(--sun); }
  .panel--coral { --accent: var(--coral); }

  .brand {
    position: absolute;
    left: 0; right: 0;
    text-align: center;
    font-family: "Cinzel", serif;
    font-weight: 400;
    color: var(--ink);
    letter-spacing: 1px;
    margin: 0;
  }
  .front .brand { top: 40px; font-size: 20px; }
  .back .brand { top: 42px; font-size: 11px; }

  .soap-window {
    position: absolute;
    left: 3px; top: 111px;
    width: 212px; height: 141px;
    background: linear-gradient(160deg, var(--soap-light), var(--soap-dark) 60%, var(--soap-light));
  }
  .scent-label {
    position: absolute;
    left: 31px; top: 0;
    width: 150px; height: 60px;
  }
  .scent-label text {
    font-family: "Cinzel", serif;
    font-size: 8.5px;
    fill: var(--ink);
    letter-spacing: 0.6px;
  }
  .tagline {
    position: absolute;
    left: 0; right: 0; top: 256px;
    text-align: center;
    font-family: "Homemade Apple", cursive;
    font-size: 10px;
    color: var(--ink);
  }
  .product {
    position: absolute;
    left: 0; right: 0; top: 268px;
    text-align: center;
    font-family: "Amatic SC", sans-serif;
    font-size: 27px;
    color: var(--ink);
    margin: 0;
  }
  .weight {
    position: absolute;
    left: 0; right: 0; top: 302px;
    text-align: center;
    font-family: "Lato", sans-serif;
    font-size: 6px;
    color: var(--ink);
  }

  .seal {
    position: absolute;
    left: 169px; top: 69px;
    width: 40px; height: 40px;
    border-radius: 50%;
    border: 1px solid #b9b9b9;
    box-sizing: border-box;
    background: var(--paper);
  }
  .ingredients {
    position: absolute;
    left: 0; right: 0; top: 126px;
    text-align: center;
    color: var(--ink);
  }
  .ingredients h2 {
    margin: 0 0 2px;
    font-family: "Cinzel", serif;
    font-weight: 400;
    font-size: 8.5px;
    letter-spacing: 0.5px;
  }
  .ingredients p {
    margin: 0;
    font-family: "Lato", sans-serif;
    font-size: 9px;
    line-height: 11.7px;
  }
  .origin {
    position: absolute;
    left: 43px; bottom: 0;
    width: 128px; height: 43px;
    border-radius: 64px 64px 0 0;
    background: var(--accent);
    font-family: "Lato", sans-serif;
    font-size: 6px;
    color: var(--ink);
    text-align: center;
    line-height: 1;
    box-sizing: border-box;
    padding-top: 28px;
  }
</style>
</head>
<body>
<div class="canvas">
  <svg class="defs" aria-hidden="true">
    <defs>
      <path id="scent-arc" d="M16 0 A59 45 0 0 0 134 0"/>
      <radialGradient id="citrus" cx="50%" cy="50%" r="50%">
        <stop offset="0" stop-color="#f7a04a"/>
        <stop offset="0.6" stop-color="#f0c043"/>
        <stop offset="1" stop-color="#8fb35a"/>
      </radialGradient>
    </defs>
  </svg>

  <!-- Fronts -->
  <section class="panel front panel--crimson" style="left:90px; top:110px;">
    <h1 class="brand">WILLOWMERE</h1>
    <div class="soap-window" role="img" aria-label="Cut-out window showing the bergamot and grapefruit soap bar">
      <svg class="scent-label" viewBox="0 0 150 60">
        <path d="M3 0 A72 58 0 0 0 147 0 Z" fill="#ffffff"/>
        <ellipse role="img" aria-label="Bergamot and grapefruit slices with leaves" cx="75" cy="12" rx="20" ry="11" fill="url(#citrus)"/>
        <text><textPath href="#scent-arc" startOffset="50%" text-anchor="middle">BERGAMOT &amp; GRAPEFRUIT</textPath></text>
      </svg>
    </div>
    <div class="tagline">Handcrafted Artisan</div>
    <h2 class="product">NATURAL SOAP</h2>
    <div class="weight">4.5 oz (127.57 grams)</div>
  </section>

  <section class="panel front panel--brick" style="left:366px; top:110px;">
    <h1 class="brand">WILLOWMERE</h1>
    <div class="soap-window" role="img" aria-label="Cut-out window showing the bergamot and grapefruit soap bar">
      <svg class="scent-label" viewBox="0 0 150 60">
        <path d="M3 0 A72 58 0 0 0 147 0 Z" fill="#ffffff"/>
        <ellipse role="img" aria-label="Bergamot and grapefruit slices with leaves" cx="75" cy="12" rx="20" ry="11" fill="url(#citrus)"/>
        <text><textPath href="#scent-arc" startOffset="50%" text-anchor="middle">BERGAMOT &amp; GRAPEFRUIT</textPath></text>
      </svg>
    </div>
    <div class="tagline">Handcrafted Artisan</div>
    <h2 class="product">NATURAL SOAP</h2>
    <div class="weight">4.5 oz (127.57 grams)</div>
  </section>

  <section class="panel front panel--sun" style="left:635px; top:107px;">
    <h1 class="brand">WILLOWMERE</h1>
    <div class="soap-window" role="img" aria-label="Cut-out window showing the bergamot and grapefruit soap bar">
      <svg class="scent-label" viewBox="0 0 150 60">
        <path d="M3 0 A72 58 0 0 0 147 0 Z" fill="#ffffff"/>
        <ellipse role="img" aria-label="Bergamot and grapefruit slices with leaves" cx="75" cy="12" rx="20" ry="11" fill="url(#citrus)"/>
        <text><textPath href="#scent-arc" startOffset="50%" text-anchor="middle">BERGAMOT &amp; GRAPEFRUIT</textPath></text>
      </svg>
    </div>
    <div class="tagline">Handcrafted Artisan</div>
    <h2 class="product">NATURAL SOAP</h2>
    <div class="weight">4.5 oz (127.57 grams)</div>
  </section>

  <section class="panel front panel--coral" style="left:911px; top:107px;">
    <h1 class="brand">WILLOWMERE</h1>
    <div class="soap-window" role="img" aria-label="Cut-out window showing the bergamot and grapefruit soap bar">
      <svg class="scent-label" viewBox="0 0 150 60">
        <path d="M3 0 A72 58 0 0 0 147 0 Z" fill="#ffffff"/>
        <ellipse role="img" aria-label="Bergamot and grapefruit slices with leaves" cx="75" cy="12" rx="20" ry="11" fill="url(#citrus)"/>
        <text><textPath href="#scent-arc" startOffset="50%" text-anchor="middle">BERGAMOT &amp; GRAPEFRUIT</textPath></text>
      </svg>
    </div>
    <div class="tagline">Handcrafted Artisan</div>
    <h2 class="product">NATURAL SOAP</h2>
    <div class="weight">4.5 oz (127.57 grams)</div>
  </section>

  <!-- Backs -->
  <section class="panel back panel--crimson" style="left:88px; top:475px;">
    <h1 class="brand">WILLOWMERE</h1>
    <div class="seal" role="img" aria-label="Ingredient-free claims seal"></div>
    <div class="ingredients">
      <h2>100% Vegan Ingredients</h2>
      <p>Olive, coconut and sunflower oils,<br>shea butter, castor oil, water,<br>bergamot and grapefruit oils,<br>pink clay, rosemary extract,<br>ground grapefruit peel, vitamin<br>E, sea salt, aloe leaf juice<br>and care.</p>
    </div>
    <div class="origin">Made in LARKVALE, CA - USA</div>
  </section>

  <section class="panel back panel--brick" style="left:366px; top:475px;">
    <h1 class="brand">WILLOWMERE</h1>
    <div class="seal" role="img" aria-label="Ingredient-free claims seal"></div>
    <div class="ingredients">
      <h2>100% Vegan Ingredients</h2>
      <p>Olive, coconut and sunflower oils,<br>shea butter, castor oil, water,<br>bergamot and grapefruit oils,<br>pink clay, rosemary extract,<br>ground grapefruit peel, vitamin<br>E, sea salt, aloe leaf juice<br>and care.</p>
    </div>
    <div class="origin">Made in LARKVALE, CA - USA</div>
  </section>

  <section class="panel back panel--sun" style="left:633px; top:475px;">
    <h1 class="brand">WILLOWMERE</h1>
    <div class="seal" role="img" aria-label="Ingredient-free claims seal"></div>
    <div class="ingredients">
      <h2>100% Vegan Ingredients</h2>
      <p>Olive, coconut and sunflower oils,<br>shea butter, castor oil, water,<br>bergamot and grapefruit oils,<br>pink clay, rosemary extract,<br>ground grapefruit peel, vitamin<br>E, sea salt, aloe leaf juice<br>and care.</p>
    </div>
    <div class="origin">Made in LARKVALE, CA - USA</div>
  </section>

  <section class="panel back panel--coral" style="left:913px; top:475px;">
    <h1 class="brand">WILLOWMERE</h1>
    <div class="seal" role="img" aria-label="Ingredient-free claims seal"></div>
    <div class="ingredients">
      <h2>100% Vegan Ingredients</h2>
      <p>Olive, coconut and sunflower oils,<br>shea butter, castor oil, water,<br>bergamot and grapefruit oils,<br>pink clay, rosemary extract,<br>ground grapefruit peel, vitamin<br>E, sea salt, aloe leaf juice<br>and care.</p>
    </div>
    <div class="origin">Made in LARKVALE, CA - USA</div>
  </section>
</div>
</body>
</html>
```